We are a recruitment company based in Norwich/Cambridge England.
I have included our company logo which we want to remain the same.

What we are looking for is a new creative Business card which will really stand out!!

Contact Information for Business Card

Harriet Dunmore
email: Harriet@plavex.co.uk
Address: Brackwell House
Fenmoor Enterprise Park
Partridge Way
Norwich
QB9 3KX
Tel:01632 960418

```html
<!DOCTYPE html>
<html lang="en">
<head>
<meta charset="utf-8">
<title>Plavex – Business Card</title>
<link rel="stylesheet" href="https://fonts.googleapis.com/css2?family=Montserrat:wght@600;700&family=Lato:wght@400;700&display=swap">
<style>
  :root {
    --backdrop: #a3a3a3;
    --card-light: #ffffff;
    --card-dark: #1c1c1c;
    --card-dark-soft: #2a2a2a;
    --brand-green: #7cc242;
    --brand-grey: #8a8789;
    --ink: #2b2b2b;
    --rule: #8f8f8f;
    --tint-green: #f1f7ea;
    --tint-grey: #f0f0f2;
  }
  * { box-sizing: border-box; margin: 0; padding: 0; }
  html, body { width: 1200px; height: 900px; overflow: hidden; }
  body {
    position: relative;
    background: var(--backdrop);
    font-family: "Lato", Arial, sans-serif;
    color: var(--ink);
  }
  .card {
    position: absolute;
    top: 170px;
    width: 347px;
    height: 560px;
    overflow: hidden;
    box-shadow: 3px 4px 6px rgba(0,0,0,0.35);
  }
  .card--front { left: 259px; background: var(--card-light); }
  .card--back { left: 631px; background: var(--card-dark); }

  .front-wash {
    position: absolute;
    left: 30px; top: 260px;
    width: 360px; height: 330px;
    border-radius: 50%;
    background: radial-gradient(ellipse at 40% 45%, var(--tint-grey) 0%, var(--tint-green) 55%, rgba(255,255,255,0) 75%);
  }

  .wordmark {
    position: absolute;
    display: flex;
    align-items: center;
    gap: 14px;
  }
  .wordmark__dot {
    width: 58px; height: 58px;
    border-radius: 50%;
    background: var(--brand-green);
  }
  .wordmark__name {
    font-family: "Montserrat", Arial, sans-serif;
    font-weight: 700;
    font-size: 44px;
    line-height: 1;
    color: var(--brand-grey);
  }
  .card--front .wordmark { left: 36px; top: 102px; }
  .card--back .wordmark { left: 28px; top: 420px; }

  .person {
    position: absolute;
    left: 0; right: 0; top: 233px;
    text-align: center;
  }
  .person__name {
    font-family: "Montserrat", Arial, sans-serif;
    font-weight: 700;
    font-size: 20px;
    letter-spacing: 0.3px;
  }
  .person__first { color: var(--brand-green); }
  .person__last { color: var(--brand-grey); }
  .person__role { font-size: 15px; margin-top: 1px; }

  .contact-block {
    position: absolute;
    left: 0; right: 0;
    text-align: center;
    font-size: 15px;
    line-height: 20.5px;
  }
  .divider {
    position: absolute;
    left: 90px; width: 167px; height: 28px;
  }
  .divider::before, .divider::after {
    content: "";
    position: absolute; top: 14px;
    width: 68px; height: 1px;
    background: var(--rule);
  }
  .divider::before { left: 0; }
  .divider::after { right: 0; }
  .divider__icon {
    position: absolute; left: 69px; top: 0;
    width: 28px; height: 28px;
    border-radius: 50%;
    background: var(--brand-green);
    display: flex; align-items: center; justify-content: center;
  }
  .divider__icon svg { width: 15px; height: 15px; fill: #fff; }

  .back-pattern {
    position: absolute;
    left: 0; top: 0; width: 100%; height: 400px;
    background: linear-gradient(180deg, var(--card-dark-soft) 0%, var(--card-dark) 100%);
  }
  .back-web {
    position: absolute;
    left: 0; right: 0; top: 511px;
    text-align: center;
    color: #fff;
    font-size: 15px;
    font-weight: 700;
  }
</style>
</head>
<body>

<section class="card card--front" aria-label="Business card front">
  <div class="front-wash" role="img" aria-label="Faint large brand decoration"></div>

  <div class="wordmark">
    <span class="wordmark__dot"></span>
    <span class="wordmark__name">Plavex</span>
  </div>

  <div class="person">
    <p class="person__name"><span class="person__first">HARRIET</span> <span class="person__last">DUNMORE</span></p>
    <p class="person__role">Managing Director</p>
  </div>

  <div class="divider" style="top:291px">
    <span class="divider__icon">
      <svg viewBox="0 0 24 24"><path d="M6.6 10.8a15.1 15.1 0 0 0 6.6 6.6l2.2-2.2c.3-.3.7-.4 1-.2 1.1.4 2.3.6 3.6.6.6 0 1 .4 1 1V20c0 .6-.4 1-1 1A17 17 0 0 1 3 4c0-.6.4-1 1-1h3.5c.6 0 1 .4 1 1 0 1.3.2 2.5.6 3.6.1.3 0 .7-.2 1z"/></svg>
    </span>
  </div>
  <div class="contact-block" style="top:323px">
    <p>(044)123456789</p>
    <p>(044)123456789</p>
    <p>(044)123456789</p>
  </div>

  <div class="divider" style="top:389px">
    <span class="divider__icon">
      <svg viewBox="0 0 24 24"><path d="M12 2a10 10 0 1 0 0 20 10 10 0 0 0 0-20zm-1 17.9A8 8 0 0 1 4.1 10L9 15v1a2 2 0 0 0 2 2zm6.9-2.5A2 2 0 0 0 16 16h-1v-3a1 1 0 0 0-1-1H8v-2h2a1 1 0 0 0 1-1V7h2a2 2 0 0 0 2-2v-.4a8 8 0 0 1 2.9 12.8z"/></svg>
    </span>
  </div>
  <div class="contact-block" style="top:419px">
    <p>info@youremail.com</p>
    <p>www.websitename.com</p>
  </div>

  <div class="divider" style="top:463px">
    <span class="divider__icon">
      <svg viewBox="0 0 24 24"><path d="M12 2a7 7 0 0 0-7 7c0 5.2 7 13 7 13s7-7.8 7-13a7 7 0 0 0-7-7zm0 9.5a2.5 2.5 0 1 1 0-5 2.5 2.5 0 0 1 0 5z"/></svg>
    </span>
  </div>
  <div class="contact-block" style="top:489px">
    <p>1234, Address GoesHere,</p>
    <p>Country name, 12345</p>
  </div>
</section>

<section class="card card--back" aria-label="Business card back">
  <div class="back-pattern" role="img" aria-label="Dark repeating brand pattern"></div>
  <div class="wordmark">
    <span class="wordmark__dot"></span>
    <span class="wordmark__name">Plavex</span>
  </div>
  <p class="back-web">www.websitename.com</p>
</section>

</body>
</html>
```